Design a compelling Tarnwove Business Card that will drive people to my site

I want a business card that I can give to people—less to tell them who I am and more to direct them to my website. My website is a portal for Pelmor Aquatics Officials and a place for people who want to become Pelmor Aquatics Officials.
I am uploading my official company logo as well as a business card mockup that I did on my own. Please feel free to completely stray from this design.
I've included a screen recording of the homepage of my website as well.
Target Market(s)
Pelmor Aquatics Officials and people who desire to become one
Contact Information for Business Card
website url
Look and feel
Each slider illustrates characteristics of the customer's brand and the style your logo design should communicate.

```html
<!DOCTYPE html>
<html lang="en">
<head>
<meta charset="utf-8">
<title>Tarnwove Business Card</title>
<link href="https://fonts.googleapis.com/css2?family=Poppins:wght@400;700;800&display=swap" rel="stylesheet">
<style>
  :root {
    --brand-blue: #3a52a5;
    --soft-blue: #8fa8dc;
    --paper: #ffffff;
    --ink-grey: #55585f;
    --stage: #1d1e21;
  }
  * { margin: 0; padding: 0; box-sizing: border-box; }
  html, body {
    width: 1200px;
    height: 900px;
    overflow: hidden;
    background: var(--stage);
    font-family: "Poppins", sans-serif;
  }
  .sheet {
    width: 1200px;
    height: 900px;
    display: flex;
    flex-direction: column;
    align-items: center;
    justify-content: center;
    gap: 30px;
  }
  .card {
    position: relative;
    width: 700px;
    height: 400px;
    overflow: hidden;
  }

  /* Front */
  .card-front { background: var(--paper); }
  .front-field {
    position: absolute;
    inset: 0;
    width: 700px;
    height: 400px;
  }
  .front-wordmark {
    position: absolute;
    left: 40px;
    top: 26px;
    font-size: 60px;
    font-weight: 800;
    letter-spacing: -1.5px;
    color: var(--brand-blue);
  }
  .front-person {
    position: absolute;
    right: 48px;
    top: 170px;
    text-align: right;
  }
  .person-name {
    font-size: 26px;
    font-weight: 800;
    color: var(--brand-blue);
    line-height: 1.2;
  }
  .person-surname { color: var(--soft-blue); }
  .person-role {
    font-size: 17px;
    font-weight: 400;
    color: var(--ink-grey);
  }
  .edge-tab {
    position: absolute;
    right: 0;
    top: 166px;
    width: 18px;
    height: 66px;
    border-radius: 9px 0 0 9px;
    background: var(--brand-blue);
  }
  .contact-list {
    position: absolute;
    right: 320px;
    top: 298px;
    list-style: none;
    text-align: right;
  }
  .contact-item {
    display: flex;
    align-items: center;
    justify-content: flex-end;
    gap: 8px;
    color: var(--paper);
    font-size: 17px;
    line-height: 26px;
  }
  .contact-icon { width: 14px; height: 14px; flex: none; }

  /* Back */
  .card-back {
    background: var(--brand-blue);
    display: flex;
    flex-direction: column;
    align-items: center;
    justify-content: center;
  }
  .back-wordmark {
    font-size: 96px;
    font-weight: 800;
    letter-spacing: -2px;
    color: var(--paper);
    line-height: 1;
  }
  .tagline-band {
    margin-top: 14px;
    width: 560px;
    padding: 8px 0;
    text-align: center;
    background: linear-gradient(90deg, rgba(143,168,220,0) 0%, rgba(143,168,220,0.45) 50%, rgba(143,168,220,0) 100%);
  }
  .tagline {
    font-size: 22px;
    font-weight: 400;
    color: var(--paper);
    letter-spacing: 0.3px;
  }
</style>
</head>
<body>
<main class="sheet">

  <section class="card card-front" aria-label="Business card front">
    <svg class="front-field" viewBox="0 0 700 400" aria-hidden="true">
      <path d="M0,60 C0,240 300,220 640,400 L0,400 Z" fill="var(--brand-blue)"/>
    </svg>
    <div class="front-wordmark">Tarnwove</div>
    <div class="front-person">
      <p class="person-name">Marcus <span class="person-surname">Ellery</span></p>
      <p class="person-role">CEO &amp; Founder</p>
    </div>
    <div class="edge-tab"></div>
    <ul class="contact-list">
      <li class="contact-item">(555) 217-4630
        <svg class="contact-icon" viewBox="0 0 16 16" aria-hidden="true"><path d="M3 1h3l1.5 4-2 1.2a9 9 0 0 0 4.3 4.3L11 8.5l4 1.5v3a2 2 0 0 1-2 2A12 12 0 0 1 1 3a2 2 0 0 1 2-2z" fill="#fff"/></svg>
      </li>
      <li class="contact-item">marcus@tarnwove.com
        <svg class="contact-icon" viewBox="0 0 16 16" aria-hidden="true"><rect x="1" y="3" width="14" height="10" rx="1.5" fill="#fff"/><path d="M1.5 4l6.5 5 6.5-5" stroke="#3a52a5" stroke-width="1.4" fill="none"/></svg>
      </li>
      <li class="contact-item">www.tarnwove.com
        <svg class="contact-icon" viewBox="0 0 16 16" aria-hidden="true"><circle cx="8" cy="8" r="7" fill="#fff"/><path d="M1 8h14M8 1c-3 3.5-3 10.5 0 14M8 1c3 3.5 3 10.5 0 14" stroke="#3a52a5" stroke-width="1.2" fill="none"/></svg>
      </li>
    </ul>
  </section>

  <section class="card card-back" aria-label="Business card back">
    <div class="back-wordmark">Tarnwove</div>
    <div class="tagline-band">
      <p class="tagline">The Trusted Deck Judge’s Gateway</p>
    </div>
  </section>

</main>
</body>
</html>
```